Bright and beautiful business card for a coach

I'm a personal and business coach based in Perth, Australia. I need a business card that whilst subtle and elegant, will stand out and appeal on a table full of cards.

My business name is Fern Mentoring and the business card must represent the warmth and brightness implied in the name, without being gimmicky. It must have a warmth and appeal and be easy to read.

I prefer clean, minimalist designs.

It must align with the feel of my website and socials: https://www.fernmentoring-example.com.au/
https://www.instagram.com/fernmentoringau/
https://www.facebook.com/fernmentoringau
Updates

Hi Designers Thank you so much for taking the time to submit designs. I wonder if I could have explained myself a little better. Most of the designs that have been submitted look rather formal and many have quite corporate looking embellishments on them (to my eye). I would like softer, warmer, more organic. I’m open to people playing about and being more abstract, using softer embellishments (e.g the line drawing flowers and grasses I’ve used in my socials) incorporating other colours from my palette or like the social icons in my email signature (in PDF), perhaps playing with size/oversize, playing with the bleed. Please don’t be constrained by what I’ve already done, it merely needs to compliment. I’m sorry if I’m not using the right words or have led you astray. I’m no designer, but I’ve done my website, socials, email signature etc all myself (my logo was a design contest) and I was really hoping for my business card to be something more creative than I could have made with a template. Reminder: No black cards/sides please. Thank you 😊

Target Market(s)

Individuals, most likely but not all female. Creative thinkers. Likely professionals.

Industry/Entity Type

Business & Personal Coach

Contact Information for Business Card

(Fern Mentoring Logo) Name: Greta Pellham; Title: Business & Personal Coach; Phone number: +61 (0)458 913307; Email: greta@fernmentoring-example.com.au; Website: https://fernmentoring-example.com.au; Social icons for Facebook, Instagram & LinkedIn: @fernmentoringAU. Optional strapline: "A thinking partner to help you cut through the noise"

Font styles to use
Sans Serif

Colors
00AB8E
00BBA5
67D7C9
C6EFE9
E9F9F6
59FF00
82FF00
B8FF75
E3FFCB
F4FFEA
FFC000
F8CF3A
FAE287
FDF2CF
FEFAEE

Requirements
Must have
• Must align with feel of my website and socials. Must have a pop of #FFC000 (possibly whole of one side, or at least a block). Bright or white background. Easy to read.
Nice to have
• Possibly incorporate the sunshine/grass picture I have used in website and socials - will upload.
Should not have
• Must not be black or dark. Not impersonal or corporate looking.

```html
<!DOCTYPE html>
<html lang="en">
<head>
<meta charset="utf-8">
<title>Fern Mentoring – Business Card</title>
<link href="https://fonts.googleapis.com/css2?family=Lato:wght@400;700&family=Sacramento&display=swap" rel="stylesheet">
<style>
  :root {
    --page-bg: #ecebe8;
    --card-bg: #ffffff;
    --sun-yellow: #ffc000;
    --gold-text: #f5b400;
    --ink: #3a3a3a;
    --grey: #6b6b6b;
    --white: #ffffff;
    --grass-dark: #2f4a1c;
    --grass-mid: #5f8a2c;
    --grass-light: #a9c566;
    --sun-glow: #f3dfc0;
  }
  * { box-sizing: border-box; margin: 0; padding: 0; }
  html, body { width: 1200px; height: 866px; overflow: hidden; }
  body {
    background: var(--page-bg);
    font-family: "Lato", sans-serif;
    color: var(--ink);
    display: flex;
    align-items: center;
    justify-content: center;
    gap: 36px;
  }
  .card {
    position: relative;
    width: 560px;
    height: 340px;
    background: var(--card-bg);
    overflow: hidden;
    box-shadow: 0 6px 18px rgba(0,0,0,0.12);
  }
  .contact-band, .strapline-band {
    position: absolute;
    left: 0; right: 0; bottom: 0;
    height: 34px;
    background: var(--sun-yellow);
    display: flex;
    align-items: center;
    justify-content: center;
    color: var(--ink);
  }
  .contact-band { font-size: 11.5px; letter-spacing: 0.2px; gap: 6px; }
  .portrait {
    position: absolute;
    left: 38px; top: 58px;
    width: 170px; height: 170px;
    background: linear-gradient(150deg, #c9cfd6 0%, #9c7f66 45%, #d9b39a 75%, #6f5a48 100%);
  }
  .identity {
    position: absolute;
    left: 236px; top: 58px;
    right: 24px;
  }
  .brand-name {
    font-size: 34px;
    font-weight: 400;
    color: var(--gold-text);
    letter-spacing: 1px;
    line-height: 1.1;
  }
  .person-name {
    font-family: "Sacramento", cursive;
    font-size: 40px;
    color: var(--gold-text);
    margin-top: 14px;
    line-height: 1;
  }
  .job-title {
    font-size: 15px;
    color: var(--ink);
    margin-top: 4px;
  }
  .social-row {
    display: flex;
    align-items: center;
    gap: 6px;
    margin-top: 14px;
    font-size: 15px;
  }
  .social-dot {
    width: 20px; height: 20px;
    border-radius: 50%;
    background: var(--sun-yellow);
  }
  .social-handle { margin-left: 6px; }

  .card-back .grass-photo {
    position: absolute;
    inset: 0 0 34px 0;
    background:
      radial-gradient(circle at 72% 28%, var(--sun-glow) 0%, rgba(243,223,192,0.6) 12%, rgba(169,197,102,0) 34%),
      linear-gradient(180deg, var(--grass-light) 0%, var(--grass-mid) 45%, var(--grass-dark) 100%);
  }
  .back-brand {
    position: absolute;
    left: 0; right: 0; top: 118px;
    text-align: center;
    font-size: 42px;
    font-weight: 400;
    color: var(--white);
    letter-spacing: 1.5px;
  }
  .strapline-band {
    font-size: 13.5px;
    letter-spacing: 0.6px;
    text-transform: uppercase;
  }
</style>
</head>
<body>
  <article class="card card-front">
    <div class="portrait" role="img" aria-label="Portrait photograph of the coach"></div>
    <div class="identity">
      <div class="brand-name">Fern Mentoring</div>
      <div class="person-name">Greta Pellham</div>
      <div class="job-title">Business &amp; Personal Coach</div>
      <div class="social-row">
        <span class="social-dot"></span>
        <span class="social-dot"></span>
        <span class="social-dot"></span>
        <span class="social-handle">@fernmentoringAU</span>
      </div>
    </div>
    <div class="contact-band">
      <span>+61 (0)458 913307</span><span>|</span>
      <span>greta@fernmentoring-example.com.au</span><span>|</span>
      <span>www.fernmentoring-example.com.au</span>
    </div>
  </article>

  <article class="card card-back">
    <div class="grass-photo" role="img" aria-label="Close-up photograph of grass with the sun shining through"></div>
    <div class="back-brand">Fern Mentoring</div>
    <div class="strapline-band">A thinking partner to help you cut through the noise</div>
  </article>
</body>
</html>
```